Exciting opportunity to create logo and a label for our natural health brand.

About us

We are a customer centric health supplement brand who believes in natural medicine and high quality ingredients. We take a holistic approach to healthcare, with an eastern philosophy. We believe in being partners with our customers in their health care journey and are invested in their well being.

Our brand philosophy and values are attached (see Vorna philosophy.png). Our personality traits are:

- Natural
- Fresh
- Modern
- Balanced (in a holistic sense)

Task breakdown

1. Design a fresh feeling logo for us
- We want it to represent our values and high quality ingredients. We would like the quality of the product to be reflected in the branding and have a high end feel.
- Logo text must include Vorna Health Sciences
- We want the Vorna to be the focus of the logo (see uploaded image Vorna logo example.png)
The logo does not have to follow this layout, but we just want the Vorna to stand out. Feel free to use your creative license on this!

2. Create an attractive label to go on the supplement bottle
- The designs need to be eye catching, give a sense of high end ingredients and natural products and tie in with the logo to give a joined up feel.
- We are selling our products online and need them to really stand out from the competition.
- See examples of labels and packaging we like (1 -7 label design).

The initial label we would like you to design would be for our product Calm Drift. It is a product that assists in the management of Anxiety and stress. The label will appear on the bottle that holds the capsules for this supplement, see uploaded files (Example plain bottles.png). The bottles may be white as the picture shows or dark blue recyclable plastic or dark brown glass . We don't have the exact dimensions of the bottle yet, but I will follow up with these.

The label needs to include the following things:
1. The logo
2. The name of the product
3. The product is to help with the relief of Anxiety and Stress
4. Number of capsules the bottle contains
5. The back of the label should have
i) The ingredients
ii) Dosage
iii) Directions of use

Please use placeholder text where needed.

We look forward to seeing your design. Thank you.

```html
<!DOCTYPE html>
<html lang="en">
<head>
<meta charset="utf-8">
<title>Vorna Health Sciences — Calm Drift label</title>
<link rel="stylesheet" href="https://fonts.googleapis.com/css2?family=Didact+Gothic&family=Quicksand:wght@500&family=Oswald:wght@400;600&display=swap">
<style>
  :root {
    --canvas-bg: #f2f1ee;
    --label-white: #ffffff;
    --gold: #e1b452;
    --gold-deep: #d8a842;
    --ink: #161616;
    --ink-soft: #222222;
  }
  * { margin: 0; padding: 0; box-sizing: border-box; }
  html, body {
    width: 1200px;
    height: 900px;
    overflow: hidden;
    background: var(--canvas-bg);
  }
  .stage {
    position: relative;
    width: 1200px;
    height: 900px;
  }
  .label {
    position: absolute;
    left: 290px;
    top: 65px;
    width: 620px;
    height: 770px;
    background: var(--label-white);
    box-shadow: 0 6px 24px rgba(0,0,0,0.08);
  }
  .label svg { display: block; }
  .brand-name {
    font-family: "Didact Gothic", sans-serif;
    fill: var(--ink);
  }
  .product-name {
    font-family: "Quicksand", sans-serif;
    font-weight: 500;
    fill: var(--label-white);
    letter-spacing: 8px;
  }
  .benefit {
    font-family: "Oswald", sans-serif;
    font-weight: 600;
    fill: var(--ink-soft);
    letter-spacing: 2.5px;
  }
  .count {
    font-family: "Oswald", sans-serif;
    font-weight: 400;
    fill: var(--ink-soft);
    letter-spacing: 1px;
  }
  .supplement-tag {
    font-family: "Oswald", sans-serif;
    font-weight: 400;
    fill: var(--ink-soft);
    letter-spacing: 1px;
  }
</style>
</head>
<body>
<main class="stage">
  <section class="label" aria-label="Calm Drift bottle label">
    <svg width="620" height="770" viewBox="0 0 620 770" xmlns="http://www.w3.org/2000/svg">
      <defs>
        <linearGradient id="goldFill" x1="0" y1="0" x2="1" y2="0">
          <stop offset="0" stop-color="var(--gold-deep)"/>
          <stop offset="0.5" stop-color="var(--gold)"/>
          <stop offset="1" stop-color="var(--gold-deep)"/>
        </linearGradient>
      </defs>

      <!-- top accent band -->
      <rect class="top-band" x="44" y="16" width="534" height="20" fill="url(#goldFill)"/>

      <!-- brand lockup -->
      <g class="brand-lockup">
        <circle cx="140" cy="150" r="62" fill="none" stroke="var(--ink)" stroke-width="2.5"/>
        <text class="brand-name" x="225" y="160" font-size="104">Vorna</text>
        <text class="brand-name" x="222" y="205" font-size="38">Health Sciences</text>
      </g>

      <!-- product name band -->
      <rect class="name-band" x="40" y="275" width="536" height="223" fill="url(#goldFill)"/>
      <text class="product-name" x="308" y="376" font-size="96" text-anchor="middle">CALM</text>
      <text class="product-name" x="308" y="476" font-size="96" text-anchor="middle">DRIFT</text>

      <!-- benefit line -->
      <text class="benefit" x="308" y="535" font-size="31" text-anchor="middle">RELIEF OF ANXIETY AND STRESS</text>

      <!-- capsule count -->
      <text class="count" x="308" y="612" text-anchor="middle"><tspan font-size="42">90</tspan><tspan font-size="34" dx="8">CAPSULES</tspan></text>

      <!-- bottom wave -->
      <path class="bottom-wave" d="M32 612 C 170 650, 360 665, 590 590 L 590 752 L 32 752 Z" fill="url(#goldFill)"/>

      <!-- supplement tag -->
      <rect class="tag-bar" x="112" y="710" width="388" height="36" fill="var(--label-white)"/>
      <text class="supplement-tag" x="306" y="738" font-size="27" text-anchor="middle">DIETARY SUPPLEMENT</text>
    </svg>
  </section>
</main>
</body>
</html>
```